Flyer, poster, banner and social media titles designs for Community Mending Chartre

The Harbourline Charter for Community Mending provide a nationally agreed framework to guide recovery policy and practice across Australia. The Principles support recovery practitioners, governments, non-government organisations and communities to deliver effective, community-centred recovery outcomes.
The Principles have recently been refreshed through extensive consultation and we require a contemporary visual identity and design suite that will increase awareness, engagement and practical application of the Principles.
The redesign will cover:
• A4 Brochure (primary publication)
• A3 Poster
• Pull up banner
• Social Media Tiles
The new design should:
• Create a recognisable brand for the Harbourline Charter.
• Appeal to both experienced and emerging recovery practitioners.
• Reflect contemporary disaster recovery practice.
• Feel people-focused rather than government-focused.
• Support future resources such as videos, implementation guides, presentations and workshop materials.
• Remain relevant for several years without requiring a major redesign.
Target Audience
• Disaster recovery practitioners
• Government agencies
• Non-government organisations
• Community recovery workers
• Recovery managers and leaders
• Community stakeholders and volunteers
The visual identity should reflect the six Principles:
• Understanding Context
• Recognising Complexity
• Community-Centred Approaches
• Coordination
• Communication
• Capacity Building
The design should communicate:
• Recovery is centred on people and communities.
• Recovery is collaborative and involves many sectors.
• Recovery is adaptive, inclusive and evidence-informed.
• Recovery supports resilience and long-term wellbeing.
• The Principles provide practical guidance for recovery practice.
We are looking for:
• Modern and professional
• Warm and approachable
• Human-centred
• Inclusive and accessible
• Australian in context
• Visually engaging
• Suitable for print and digital use
We would like to avoid:
• Images of disaster destruction
• Emergency response imagery (fire trucks, flashing lights, etc.)
• Overly corporate or bureaucratic designs
• Designs that focus on deficits rather than recovery and growth
Consider themes such as:
• Connection and collaboration
• Communities and people
• Growth, recovery and renewal
Accessibility
Designs should:
• Meet accessibility best practice
• Use clear typography
• Achieve strong colour contrast
• Be suitable for both digital and print formats

Deliverables
1. Principles Brochure
• A4 trifold size x 2 (online and print friendly version)
• A side to include cover side, logos side and overview of principles.
• B side full details of the principles
• Graphic to highlight the 3 c’s concept (RECOVERY Context, complexity, community centred, coordinate, communicate and capacity). Currently 3 circles.
• Can be printed and distributed electronically
2. Poster
• A1 and A3 versions
• Suitable for office and workshop display
3. Pull-Up Banner - 850 mm (W) × 2000 mm (H)
• Conference and event use
• High visual impact
• Strong branding and concise messaging
4. Social Media Tiles x 3

We are providing an extension and increasing the budget following feedback from designers. We are wanting the resources to look and feel different from the existing designs, considering either a different colour palette in the designs or different motif with the leave design. Any nature based designs should consider the Australian fauna or flora. Also suggest avoiding images in the designs. The principles are not numbered or liner in the concept of how they function. Happy to answer any further questions and thank you for your suggested concepts.

Disaster recovery practitioners, Government agencies , Non-government organisations, Community recovery workers and Community stakeholders and volunteers

Disaster recovery

• Modern, warm, visually engaging, human-centred, Australian in context and different to the current design.
• Symbols for each principles
• Images of disaster destruction, Emergency response imagery, Overly corporate or bureaucratic designs, Designs that focus on deficits rather than recovery and growth, avoid too much black

```html
<!DOCTYPE html>
<html lang="en">
<head>
<meta charset="utf-8">
<title>Harbourline Charter for Community Mending – Trifold Brochure</title>
<link href="https://fonts.googleapis.com/css2?family=Cinzel:wght@400;600;700&family=Inter:wght@300;400;500;600&display=swap" rel="stylesheet">
<style>
:root{
  --stage:#2d2d2d;
  --green:#4b7a2b;
  --green-light:#5b8f35;
  --green-mid:#4f8330;
  --green-deep:#3f6b24;
  --ink:#222222;
  --paper:#ffffff;
  --body-grey:#5a5a5a;
  --soft-grey:#8a8a8a;
  --petal:#d98a76;
  --leaf:#9bb783;
}
*{box-sizing:border-box;margin:0;padding:0}
html,body{width:789px;height:1200px;overflow:hidden;background:var(--stage)}
body{position:relative;font-family:"Inter",sans-serif}
.spread{position:absolute;left:76px;width:636px;height:491px;display:flex}
.spread--outer{top:73px}
.spread--inner{top:636px}
.panel{position:relative;width:212px;height:100%;overflow:hidden}
.panel--green{background:var(--green);color:var(--paper)}
.panel--white{background:var(--paper);color:var(--body-grey)}

/* outer left panel */
.overview{padding:20px 19px 0 19px}
.overview__kicker{font-size:8.4px;font-weight:400;letter-spacing:.2px}
.overview__title{font-family:"Cinzel",serif;font-weight:700;font-size:13.4px;letter-spacing:.3px;margin-top:2px;line-height:1.1;white-space:nowrap}
.overview__text{font-size:4.7px;line-height:8.5px;text-align:justify;margin-top:6px}
.overview__text p+p{margin-top:8.5px}
.overview__heading{font-family:"Cinzel",serif;font-weight:600;font-size:8.6px;margin-top:9px;letter-spacing:.2px}
.summary{list-style:none;margin-top:6px}
.summary__item{display:flex;gap:8px;height:32.5px}
.summary__icon{flex:0 0 20px;height:20px;border-radius:50%;background:var(--paper);display:flex;align-items:center;justify-content:center}
.summary__name{font-size:4.8px;font-weight:500;line-height:7px;margin-top:-1px}
.summary__desc{font-size:4.1px;line-height:6.6px;opacity:.9;text-align:justify}

/* outer middle panel */
.partners__arch{position:absolute;left:0;top:62px;width:212px;height:429px;background:var(--paper);border-radius:106px 106px 0 0}
.card{position:absolute;background:var(--paper);border-radius:6px;box-shadow:0 1px 5px rgba(0,0,0,.13);display:flex;align-items:center;justify-content:center;gap:3px;text-align:center;font-family:"Inter",sans-serif;font-weight:600;color:var(--green-deep);font-size:5.4px;line-height:6.6px;padding:3px}
.card__dot{flex:0 0 7px;height:7px;border-radius:50%;background:var(--green-deep)}
.partners__band{position:absolute;left:0;top:387px;width:212px;height:29px;background:var(--ink);color:var(--paper);font-size:8.6px;font-weight:500;display:flex;align-items:center;justify-content:center;letter-spacing:.2px}

/* outer right panel */
.cover{text-align:center}
.cover__kicker{position:absolute;top:36px;left:0;width:212px;font-size:8.6px;font-weight:400}
.cover__title{position:absolute;top:52px;left:0;width:212px;font-family:"Cinzel",serif;font-weight:700;line-height:1}
.cover__title span{display:block;white-space:nowrap}
.cover__title .l1{font-size:25px}
.cover__title .l2{font-size:21px;margin-top:5px}
.cover__art{position:absolute;left:19px;top:138px;width:181px;height:154px;border-radius:50%;background:radial-gradient(circle at 50% 45%,#e9b89a 0%,var(--petal) 35%,#c9735f 55%,var(--leaf) 78%,rgba(155,183,131,0) 100%)}
.cover__wheel{position:absolute;left:25px;top:290px;width:170px;height:170px}

/* inner panels */
.principle{position:absolute;left:19px;width:175px}
.principle__head{display:flex;align-items:flex-start;gap:13px}
.principle__icon{flex:0 0 27px;height:27px;border-radius:50%;display:flex;align-items:center;justify-content:center}
.panel--white .principle__icon{background:var(--green)}
.panel--green .principle__icon{background:var(--paper)}
.principle__small{font-family:"Cinzel",serif;font-weight:400;font-size:8.6px;letter-spacing:.4px;line-height:10px;white-space:nowrap}
.principle__big{font-family:"Cinzel",serif;font-weight:700;font-size:15.2px;letter-spacing:.3px;line-height:16px;white-space:nowrap}
.principle__big--long{font-size:13.4px;letter-spacing:0}
.panel--white .principle__big{color:var(--green)}
.panel--white .principle__small{color:#3a3a3a}
.principle__intro{font-size:5.4px;line-height:8.8px;text-align:justify;margin-top:12px}
.panel--white .principle__intro{color:#333}
.principle__list{list-style:none;margin-top:7px;font-size:4.95px;line-height:10.2px;text-align:justify}
.principle__list li::before{content:"•";margin:0 4px 0 1px}
.panel--white .principle__list{color:var(--soft-grey)}
.divider{position:absolute;left:19px;width:175px;border-top:.6px dashed #b5b5b5}
.panel--green .divider{border-color:rgba(255,255,255,.55)}
</style>
</head>
<body>

<section class="spread spread--outer">
  <article class="panel panel--green overview">
    <p class="overview__kicker">HARBOURLINE CHARTER FOR</p>
    <h2 class="overview__title">COMMUNITY MENDING</h2>
    <div class="overview__text">
      <p>Disasters can deeply impact lives and livelihoods. Working with communities recovering from disasters is complex and challenging. Recovery is long-term, non-linear and dynamic, particularly in the context of compounding and concurrent disasters. These principles are a way to guide our efforts, our approach, our planning and our decision-making.</p>
      <p>Disaster recovery is part of emergency management, which includes the broader components of prevention, preparedness and response. Planning for recovery is integral to emergency preparation, and mitigation actions are often initiated as part of recovery.</p>
      <p>Disaster recovery includes built, environmental and economic elements, as well as individual and social wellbeing. Recovery can provide an opportunity to improve these aspects beyond previous conditions, by enhancing social and natural environments, infrastructure and economies –contributing to more resilient communities.</p>
      <p>The relationship between the principles<br>While all the principles are equally critical to ensure effective recovery, understanding the local and broader context and recognising complexity are foundational. The descriptions beneath each principle provide further guidance for working with communities in disaster recovery.</p>
    </div>
    <h3 class="overview__heading">SUCCESSFUL RECOVERY</h3>
    <ul class="summary">
      <li class="summary__item">
        <span class="summary__icon"><svg width="11" height="11" viewBox="0 0 12 12" fill="none" stroke="#4b7a2b" stroke-width="1"><rect x="1.5" y="1.5" width="7" height="5" rx="1"/><circle cx="8" cy="8" r="2"/><path d="M5 11h6"/></svg></span>
        <div><p class="summary__name">Understand the CONTEXT</p><p class="summary__desc">Successful recovery is based on an understanding of the community context, with each community having its own history, values and dynamics.</p></div>
      </li>
      <li class="summary__item">
        <span class="summary__icon"><svg width="12" height="12" viewBox="0 0 12 12" fill="none" stroke="#4b7a2b" stroke-width=".9"><circle cx="6" cy="6" r="5"/><circle cx="6" cy="6" r="3"/><circle cx="6" cy="6" r="1"/></svg></span>
        <div><p class="summary__name">Recognise COMPLEXITY</p><p class="summary__desc">Successful recovery is responsive to the complex and evolving nature of disasters and their impacts on communities, including compounding, cascading and concurrent events.</p></div>
      </li>
      <li class="summary__item">
        <span class="summary__icon"><svg width="12" height="12" viewBox="0 0 12 12" fill="none" stroke="#4b7a2b" stroke-width=".9"><circle cx="6" cy="6" r="5"/><path d="M6 1.5 10 4.5 8.5 9.5h-5L2 4.5Z"/></svg></span>
        <div><p class="summary__name">Use COMMUNITY-CENTRED approaches</p><p class="summary__desc">Successful recovery is community-centred, responsive and flexible, engaging with community and supporting them to move forward, with shared responsibilities.</p></div>
      </li>
      <li class="summary__item">
        <span class="summary__icon"><svg width="12" height="12" viewBox="0 0 12 12" fill="none" stroke="#4b7a2b" stroke-width=".9"><circle cx="6" cy="6" r="5"/><circle cx="6" cy="4.5" r="1.3"/><path d="M3.5 9c.5-1.8 1.4-2.6 2.5-2.6S8 7.2 8.5 9"/></svg></span>
        <div><p class="summary__name">COORDINATE all activities</p><p class="summary__desc">Successful recovery requires a planned, coordinated and adaptive approach, between community and partner agencies, based on continuing assessment of impacts and needs.</p></div>
      </li>
      <li class="summary__item">
        <span class="summary__icon"><svg width="12" height="12" viewBox="0 0 12 12" fill="none" stroke="#4b7a2b" stroke-width=".9"><circle cx="3" cy="3" r="1.5"/><circle cx="9" cy="3" r="1.5"/><circle cx="6" cy="9" r="1.5"/><path d="M4.2 4 5.4 7.8M7.8 4 6.6 7.8M4.5 3h3"/></svg></span>
        <div><p class="summary__name">COMMUNICATE effectively</p><p class="summary__desc">Successful recovery is built on effective communication between the affected community and other partners.</p></div>
      </li>
      <li class="summary__item">
        <span class="summary__icon"><svg width="12" height="12" viewBox="0 0 12 12" fill="none" stroke="#4b7a2b" stroke-width=".9"><rect x="1.5" y="1.5" width="8" height="8"/><path d="M3.5 8V6M5.5 8V4.5M7.5 8V3"/><circle cx="9" cy="9" r="1.5"/></svg></span>
        <div><p class="summary__name">Recognise and build CAPACITY</p><p class="summary__desc">Successful recovery recognises, supports and builds on individual, community and organisational capacity and resilience.</p></div>
      </li>
    </ul>
  </article>

  <article class="panel panel--green partners">
    <div class="partners__arch"></div>
    <div class="card" style="left:80px;top:90px;width:52px;height:35px">Southgate State Office</div>
    <div class="card" style="left:18px;top:140px;width:81px;height:51px">Federal Community Services</div>
    <div class="card" style="left:112px;top:140px;width:81px;height:51px">Federal Civic Affairs</div>
    <div class="card" style="left:18px;top:206px;width:49px;height:51px">Helping Hands Aid</div>
    <div class="card" style="left:75px;top:206px;width:49px;height:51px">Northreach Government</div>
    <div class="card" style="left:132px;top:206px;width:61px;height:51px">Midland Government</div>
    <div class="card" style="left:18px;top:271px;width:50px;height:50px">Westcoast Government</div>
    <div class="card" style="left:79px;top:271px;width:54px;height:50px">Capital Region Office</div>
    <div class="card" style="left:140px;top:271px;width:54px;height:50px">Islandvale Government</div>
    <div class="card" style="left:18px;top:336px;width:72px;height:35px"><span class="card__dot"></span>Topend Territory</div>
    <div class="card" style="left:99px;top:336px;width:94px;height:35px">Eastshore Emergency Office</div>
    <div class="partners__band">PARTNERS IN DEVELOPMENT FROM THE</div>
    <div class="card" style="left:58px;top:429px;width:95px;height:43px"><span class="card__dot"></span>Recovery Reference Circle</div>
  </article>

  <article class="panel panel--green cover">
    <p class="cover__kicker">HARBOURLINE CHARTER FOR</p>
    <h1 class="cover__title"><span class="l1">COMMUNITY</span><span class="l2">MENDING</span></h1>
    <div class="cover__art" role="img" aria-label="Illustration of a banksia flower surrounded by soft coral and sage circles"></div>
    <svg class="cover__wheel" viewBox="-85 -85 170 170" role="img" aria-label="Recovery wheel linking the six principles">
      <defs>
        <path id="arcTL" d="M -68 0 A 68 68 0 0 1 0 -68"/>
        <path id="arcTR" d="M 0 -68 A 68 68 0 0 1 68 0"/>
        <path id="arcBR" d="M 73 0 A 73 73 0 0 1 0 73"/>
        <path id="arcBL" d="M 0 73 A 73 73 0 0 1 -73 0"/>
        <path id="arcTop" d="M -35 0 A 35 35 0 0 1 35 0"/>
        <path id="arcBot" d="M 39 0 A 39 39 0 0 1 -39 0"/>
        <radialGradient id="ringShade" r="0.5">
          <stop offset="0.6" stop-color="#3f6b24"/>
          <stop offset="1" stop-color="#5b8f35"/>
        </radialGradient>
      </defs>
      <path d="M0 0 L -82 0 A 82 82 0 0 1 0 -82 Z" fill="var(--green-mid)"/>
      <path d="M0 0 L 0 -82 A 82 82 0 0 1 82 0 Z" fill="var(--green-light)"/>
      <path d="M0 0 L 82 0 A 82 82 0 0 1 0 82 Z" fill="var(--green-mid)"/>
      <path d="M0 0 L 0 82 A 82 82 0 0 1 -82 0 Z" fill="var(--green-light)"/>
      <circle r="62" fill="url(#ringShade)"/>
      <circle r="48" fill="#222"/>
      <circle r="24" fill="#fff"/>
      <g font-family="Inter, sans-serif" font-size="8" fill="#fff" letter-spacing="1">
        <text><textPath href="#arcTL" startOffset="50%" text-anchor="middle">COORDINATE</textPath></text>
        <text><textPath href="#arcTR" startOffset="50%" text-anchor="middle">CONTEXT</textPath></text>
        <text><textPath href="#arcBR" startOffset="50%" text-anchor="middle">COMPLEXITY</textPath></text>
        <text><textPath href="#arcBL" startOffset="50%" text-anchor="middle">COMMUNITY-CENTRED</textPath></text>
        <text font-size="7.4"><textPath href="#arcTop" startOffset="50%" text-anchor="middle">COMMUNICATE</textPath></text>
        <text font-size="7.4"><textPath href="#arcBot" startOffset="50%" text-anchor="middle">RECOGNISE</textPath></text>
      </g>
      <text y="2.5" text-anchor="middle" font-family="Inter, sans-serif" font-size="6.6" fill="#4b7a2b">RECOVERY</text>
    </svg>
  </article>
</section>

<section class="spread spread--inner">
  <article class="panel panel--white">
    <div class="principle" style="top:19px">
      <div class="principle__head">
        <span class="principle__icon"><svg width="14" height="14" viewBox="0 0 12 12" fill="none" stroke="#fff" stroke-width=".8"><rect x="1.5" y="1.5" width="7" height="5" rx="1"/><circle cx="8" cy="8" r="2"/><path d="M5 11h6"/></svg></span>
        <div><p class="principle__small" style="margin-top:1px">UNDERSTAND THE</p><h3 class="principle__big">CONTEXT</h3></div>
      </div>
      <p class="principle__intro">Successful recovery is based on an understanding of the community context, with each community having its own history, values and dynamics. Recovery should:</p>
      <ul class="principle__list">
        <li>Acknowledge existing strengths and capacity, including past experiences and future aspirations;</li>
        <li>Appreciate the risks and stressors faced by the community;</li>
        <li>Embed accessibility, equity, inclusion and diversity in recovery practice, using culturally safe and trauma-informed approaches;</li>
        <li>Support people who may be at greater risk or disproportionately impacted;</li>
        <li>Respect and support connections to Country, environment, animals and culturally significant places and recognise environmental regeneration in recovery;</li>
        <li>Recognise pathways and timeframes vary; systems should support long-term recovery shaped by community needs; and</li>
        <li>Acknowledge the impact upon the community may extend beyond the geographical boundaries where the disaster occurred.</li>
      </ul>
    </div>
    <div class="divider" style="top:245px"></div>
    <div class="principle" style="top:263px">
      <div class="principle__head">
        <span class="principle__icon"><svg width="14" height="14" viewBox="0 0 12 12" fill="none" stroke="#fff" stroke-width=".8"><circle cx="6" cy="6" r="5"/><circle cx="6" cy="6" r="3"/><circle cx="6" cy="6" r="1"/></svg></span>
        <div><p class="principle__small" style="margin-top:3px">RECOGNISE</p><h3 class="principle__big">COMPLEXITY</h3></div>
      </div>
      <p class="principle__intro">Successful recovery is responsive to the complex and evolving nature of disasters and their impacts on communities, including compounding, cascading and concurrent events. Recovery should recognise that:</p>
      <ul class="principle__list">
        <li>Disasters lead to a range of effects and impacts that require a variety of approaches; they can also leave long-term legacies;</li>
        <li>Information on impacts and needs can be limited at first and changes over time;</li>
        <li>Affected individuals and the community have diverse needs, wants and expectations, which can evolve rapidly;</li>
        <li>Responsive and flexible action is crucial to addressing immediate needs;</li>
        <li>Existing community knowledge and values may challenge the assumptions of those outside of the community;</li>
        <li>Conflicting knowledge, values and priorities among individuals, the community and organisations may create tensions;</li>
        <li>Emergencies create stressful environments where grief or blame may also affect those involved;</li>
      </ul>
    </div>
  </article>

  <article class="panel panel--green">
    <div class="principle" style="top:19px">
      <div class="principle__head">
        <span class="principle__icon"><svg width="14" height="14" viewBox="0 0 12 12" fill="none" stroke="#4b7a2b" stroke-width=".8"><circle cx="6" cy="6" r="5"/><path d="M6 1.5 10 4.5 8.5 9.5h-5L2 4.5Z"/></svg></span>
        <div><p class="principle__small" style="margin-top:1px">USE</p><h3 class="principle__big principle__big--long">COMMUNITY-LED</h3></div>
      </div>
      <p class="principle__intro">Successful recovery is community-centred, responsive and flexible, engaging with community and supporting them to move forward, with shared responsibilities. Recovery should:</p>
      <ul class="principle__list">
        <li>Assist and enable individuals, families and the community to actively participate in their own recovery;</li>
        <li>Recognise that individuals and the community may need different levels of support at various times;</li>
        <li>Be guided by the communities' priorities;</li>
        <li>Channel effort through pre-identified and existing community assets, including local knowledge, existing community strengths and resilience;</li>
        <li>Build collaborative partnerships that reflect diverse representation and community leadership in recovery;</li>
        <li>Support Aboriginal and Torres Strait Islander self-determination and Indigenous governance, recognising Country as central to recovery and resilience;</li>
        <li>Recognise that new community leaders often emerge during and after a disaster, who may not hold formal positions of authority;</li>
      </ul>
    </div>
    <div class="divider" style="top:247px"></div>
    <div class="principle" style="top:263px">
      <div class="principle__head">
        <span class="principle__icon"><svg width="14" height="14" viewBox="0 0 12 12" fill="none" stroke="#4b7a2b" stroke-width=".8"><circle cx="6" cy="6" r="5"/><circle cx="6" cy="4.5" r="1.3"/><path d="M3.5 9c.5-1.8 1.4-2.6 2.5-2.6S8 7.2 8.5 9"/></svg></span>
        <div><h3 class="principle__big">COORDINATE</h3><p class="principle__small" style="margin-top:2px">ALL ACTIVITIES</p></div>
      </div>
      <p class="principle__intro">Successful recovery requires a planned, coordinated and adaptive approach, between community and partner agencies, based on continuing assessment of impacts and need. Recovery should:</p>
      <ul class="principle__list">
        <li>Have clearly articulated and shared goals based on desired outcomes;</li>
        <li>Be flexible, taking into account changes in community needs or stakeholder expectations;</li>
        <li>Be guided by those with experience and expertise, using skilled, authentic and capable community leadership;</li>
        <li>Be at the pace desired by the community, and seek to collaborate and reconcile different interests and time frames;</li>
        <li>Reflect well-developed community planning and information gathering before, during and after a disaster;</li>
        <li>Have clear decision-making and reporting structures and sound governance, which are transparent and accessible to the community;</li>
        <li>Demonstrate an understanding of the roles, responsibilities and authority of organisations involved and coordinate across agencies to ensure minimal service provision disruption;</li>
      </ul>
    </div>
  </article>

  <article class="panel panel--white">
    <div class="principle" style="top:19px">
      <div class="principle__head">
        <span class="principle__icon"><svg width="14" height="14" viewBox="0 0 12 12" fill="none" stroke="#fff" stroke-width=".8"><circle cx="3" cy="3" r="1.5"/><circle cx="9" cy="3" r="1.5"/><circle cx="6" cy="9" r="1.5"/><path d="M4.2 4 5.4 7.8M7.8 4 6.6 7.8M4.5 3h3"/></svg></span>
        <div><h3 class="principle__big">COMMUNICATE</h3><p class="principle__small" style="margin-top:2px">EFFECTIVELY</p></div>
      </div>
      <p class="principle__intro">Successful recovery is built on effective communication between the affected community and other partners. Recovery should:</p>
      <ul class="principle__list">
        <li>Recognise that communication should be two-way, transparent and ongoing, building trust through shared understanding and feedback;</li>
        <li>Ensure that information is accessible to audiences in diverse situations, addresses a variety of communication needs, and is provided through a range of communication channels and networks;</li>
        <li>Establish mechanisms for coordinated and consistent communications between all service providers, organisations and individuals and the community;</li>
        <li>Ensure that all communication is relevant, timely, clear, accurate, targeted, credible and consistent; and</li>
        <li>Identify trusted sources of information and repeat key recovery messages to enable greater community confidence and receptivity.</li>
      </ul>
    </div>
    <div class="divider" style="top:212px"></div>
    <div class="principle" style="top:228px">
      <div class="principle__head">
        <span class="principle__icon"><svg width="14" height="14" viewBox="0 0 12 12" fill="none" stroke="#fff" stroke-width=".8"><rect x="1.5" y="1.5" width="8" height="8"/><path d="M3.5 8V6M5.5 8V4.5M7.5 8V3"/><circle cx="9" cy="9" r="1.5"/></svg></span>
        <div><p class="principle__small" style="margin-top:3px">RECOGNISE AND BUILD</p><h3 class="principle__big">CAPACITY</h3></div>
      </div>
      <p class="principle__intro">Successful recovery recognises, supports and builds on individual, community and organisational capacity and resilience. Recovery should:</p>
      <ul class="principle__list">
        <li>Assess capability and capacity requirements before, during and after a disaster;</li>
        <li>Support the development of self-reliance, preparation and disaster mitigation;</li>
        <li>Quickly identify and mobilise community skills, strengths and resources;</li>
        <li>Develop networks and partnerships to strengthen capacity, capability and resilience;</li>
        <li>Support training and knowledge sharing to sustain recovery capability across staff, volunteers, and the community;</li>
        <li>Ensure mental health and wellbeing supports are available for staff, volunteers and communities involved in disaster recovery;</li>
        <li>Recognise that resources can be provided by a range of partners and from community networks;</li>
        <li>Acknowledge that existing resources may be stretched, and that additional resources may be required;</li>
        <li>Understand that additional resources may only be available for a limited period, and that sustainability may need to be addressed;</li>
      </ul>
    </div>
  </article>
</section>

</body>
</html>
```